Modern Label for cleaning products for the brand Vorlix

We need a label design for our line of cleaning products. The label should feature our logo and an image to identify the product's intended use. I've added our logo and an image for use. This only concerns the design of the label on the front of the bottle.

Label dimensions:
Label 1 (500ml bottle with spray): width 58mm x height 115mm
Label 2: (1L bottle): width 73mm x height 140mm
The design must be consistent for both bottles which you find in the pictures.

The bottles to be labeled are white. See the attachment for a photo of the bottles.

The photo must also appear on the label to identify the product's intended use.

Product information:
Brand: Vorlix
Product: Sanitary Cleaner

This text must be placed on the label:
"Cleans, descales & freshens. followed with this text: "Ideal for quick and powerful cleaning. A ready-to-use product for everyday use."

- Mention the seperate USP's: Sanitary, Bathroom, Toilet, Wet areas

Appearance: This is a consumer product, but it must have a professional appearance. We would like to see a design that use the color blue from our logo.

Target Market(s)

Consumers who take care of their homes and want to maintain it the correct (professional) way

Font styles to use
Sans Serif

Colors
0054AA
0677BA
7BADD7
CADEEF
E8F1F8

Requirements
Must have
• USP's + use of image and logo + blend in 1 design
Nice to have
• Keep the color of the logo in the design
Should not have
• Comic sans

```html
<!DOCTYPE html>
<html lang="en">
<head>
<meta charset="utf-8">
<title>Vorlix Sanitary Cleaner – Front Label</title>
<link rel="stylesheet" href="https://fonts.googleapis.com/css2?family=Montserrat:wght@400;500;700;800&family=Oswald:wght@500&display=swap">
<style>
  :root {
    --blue-deep: #0054AA;
    --blue-main: #0677BA;
    --blue-bright: #1a8fd6;
    --blue-soft: #7BADD7;
    --blue-pale: #CADEEF;
    --blue-mist: #E8F1F8;
    --ink: #111318;
    --white: #ffffff;
    --tagline: #1a9ad6;
  }
  * { box-sizing: border-box; margin: 0; padding: 0; }
  html, body { width: 1200px; height: 784px; overflow: hidden; background: #ffffff; }
  body { position: relative; font-family: "Montserrat", Arial, sans-serif; }

  .label {
    position: absolute; left: 421px; top: 36px;
    width: 358px; height: 712px;
    border-radius: 14px; overflow: hidden;
    background: radial-gradient(ellipse at 50% 28%, var(--white) 0%, var(--blue-mist) 30%, var(--blue-pale) 75%, #bcd2e6 100%);
  }

  .label__header { position: absolute; left: 0; top: 0; width: 358px; height: 112px; }

  .brand {
    position: absolute; left: 0; top: 44px; width: 358px;
    display: flex; align-items: center; justify-content: center; gap: 9px;
  }
  .brand__dot { width: 26px; height: 26px; border-radius: 50%; background: var(--white); }
  .brand__name { font-weight: 800; font-size: 30px; color: var(--white); letter-spacing: -0.5px; line-height: 1; }

  .bubble {
    position: absolute; border-radius: 50%;
    border: 2px solid rgba(6, 119, 186, 0.55);
    background: radial-gradient(circle at 35% 35%, rgba(255,255,255,0.9), rgba(202,222,239,0.25) 60%, rgba(123,173,215,0.35));
  }

  .product-title {
    position: absolute; left: 0; top: 182px; width: 358px;
    text-align: center; font-weight: 800; color: var(--ink);
    font-size: 52px; line-height: 0.92; letter-spacing: -0.5px;
  }

  .tagline {
    position: absolute; left: 0; top: 331px; width: 358px; text-align: center;
    font-family: "Oswald", "Arial Narrow", sans-serif; font-weight: 500;
    font-size: 16px; color: var(--tagline); letter-spacing: 0.2px;
  }
  .claim {
    position: absolute; left: 0; top: 362px; width: 358px; text-align: center;
    font-weight: 800; font-size: 17px; line-height: 1.05; color: var(--ink); letter-spacing: -0.3px;
  }

  .usage-photo {
    position: absolute; left: 0; top: 406px; width: 358px; height: 180px;
    background: linear-gradient(90deg, #6f7275 0%, #9a9c9e 22%, #dcdfe2 45%, #eef0f2 65%, #c7cacd 88%, #8d9092 100%);
  }

  .volume {
    position: absolute; left: 242px; top: 580px; width: 88px; height: 33px;
    background: var(--white); border-radius: 17px; text-align: center; z-index: 3;
    border: 1px solid var(--blue-pale);
  }
  .volume__amount { display: block; font-weight: 700; font-size: 15px; color: var(--ink); line-height: 1; margin-top: 5px; }
  .volume__unit { display: block; font-weight: 400; font-size: 7px; color: #666; letter-spacing: 0.3px; }

  .label__footer {
    position: absolute; left: 0; top: 586px; width: 358px; height: 126px;
    background: linear-gradient(180deg, var(--blue-bright) 0%, var(--blue-main) 100%);
    color: var(--white);
  }
  .suitable__heading { position: absolute; left: 42px; top: 14px; font-size: 9px; font-weight: 500; letter-spacing: 0.2px; }
  .suitable__list { position: absolute; left: 18px; top: 34px; width: 322px; display: flex; justify-content: space-between; list-style: none; }
  .suitable__item { width: 74px; display: flex; flex-direction: column; align-items: center; gap: 10px; font-size: 9px; font-weight: 500; }
  .suitable__item svg { width: 22px; height: 22px; fill: var(--white); }
  .footer-note { position: absolute; left: 0; top: 97px; width: 358px; text-align: center; font-size: 8.5px; font-weight: 500; }
  .footer-note strong { font-weight: 800; }
</style>
</head>
<body>
  <main class="label">
    <svg class="label__header" viewBox="0 0 358 112" aria-hidden="true">
      <defs>
        <linearGradient id="header-fill" x1="0" y1="0" x2="0" y2="1">
          <stop offset="0" stop-color="#0677BA"/>
          <stop offset="1" stop-color="#1a8fd6"/>
        </linearGradient>
      </defs>
      <path d="M0 0 H358 V88 Q179 130 0 88 Z" fill="url(#header-fill)"/>
    </svg>

    <div class="brand">
      <span class="brand__dot"></span>
      <span class="brand__name">Vorlix</span>
    </div>

    <span class="bubble" style="left:304px;top:136px;width:30px;height:30px"></span>
    <span class="bubble" style="left:23px;top:204px;width:25px;height:25px"></span>
    <span class="bubble" style="left:14px;top:242px;width:15px;height:15px"></span>
    <span class="bubble" style="left:318px;top:270px;width:48px;height:48px"></span>
    <span class="bubble" style="left:-4px;top:336px;width:36px;height:36px"></span>
    <span class="bubble" style="left:313px;top:388px;width:24px;height:24px"></span>

    <h1 class="product-title">Sanitary<br>Cleaner</h1>

    <p class="tagline">-CLEANS, DESCALES &amp; FRESHENS-</p>
    <p class="claim">Ideal for quick and<br>powerful cleaning.</p>

    <div class="usage-photo" role="img" aria-label="Photo of a bright modern bathroom with walk-in shower, washbasin, bathtub and towel radiator"></div>

    <div class="volume">
      <span class="volume__amount">500ML</span>
      <span class="volume__unit">NET WT</span>
    </div>

    <section class="label__footer">
      <p class="suitable__heading">SUITABLE FOR:</p>
      <ul class="suitable__list">
        <li class="suitable__item">
          <svg viewBox="0 0 24 24" aria-hidden="true"><path d="M12 2 L21 5 V11 C21 17 17 21 12 23 C7 21 3 17 3 11 V5 Z"/></svg>
          SANITARY
        </li>
        <li class="suitable__item">
          <svg viewBox="0 0 24 24" aria-hidden="true"><path d="M9 3 H13 V5 H11 V9 H9 Z M3 11 H21 V13 C21 17 18 20 14 20 H10 C6 20 3 17 3 13 Z"/></svg>
          BATHROOM
        </li>
        <li class="suitable__item">
          <svg viewBox="0 0 24 24" aria-hidden="true"><path d="M6 2 H10 V11 H19 V13 C19 16 17 18 15 18.5 V22 H9 V18 C7 17 6 15 6 13 Z"/></svg>
          TOILET
        </li>
        <li class="suitable__item">
          <svg viewBox="0 0 24 24" aria-hidden="true"><path d="M8 3 L9.5 8 L14 9.5 L9.5 11 L8 16 L6.5 11 L2 9.5 L6.5 8 Z M17 8 L18.2 11.8 L22 13 L18.2 14.2 L17 18 L15.8 14.2 L12 13 L15.8 11.8 Z M10 17 L10.7 19.3 L13 20 L10.7 20.7 L10 23 L9.3 20.7 L7 20 L9.3 19.3 Z"/></svg>
          WET AREAS
        </li>
      </ul>
      <p class="footer-note">A <strong>READY-TO-USE PRODUCT</strong> FOR EVERYDAY USE.</p>
    </section>
  </main>
</body>
</html>
```